Business Card Design for company

We want new business cards. We'd like something different-- yet still highly professional. Our tagline is Offering direction, achieving results. Stock photos are ok, as long as they are relevant and look upscale.

Target Market(s)

Architecture/Business Management Consulting/Engineering Consulting

Contact Information for Business Card

dark gray background with pops of blue might be good, but you tell me. You're the designers. Rounded corners might be nice, but again, you tell me.

Font styles to use
Serif
Sans Serif

Colors
3276b5
5c5c5c
9d9d9d
fbfbfb

Requirements
Nice to have
• Something different, but still very professional.

```html
<!DOCTYPE html>
<html lang="en">
<head>
<meta charset="utf-8">
<title>Norvale Advisory – Business Card</title>
<link rel="stylesheet" href="https://fonts.googleapis.com/css2?family=Roboto:wght@400;500;700&display=swap">
<style>
  :root {
    --backdrop: #1c1c1d;
    --brand-blue: #286296;
    --ink-gray: #4f5257;
    --text-light: #f4f6f9;
    --card-white: #ffffff;
  }
  * { margin: 0; padding: 0; box-sizing: border-box; }
  html, body {
    width: 1125px;
    height: 1200px;
    overflow: hidden;
    background: var(--backdrop);
    font-family: "Roboto", Arial, sans-serif;
  }
  .stage {
    position: relative;
    width: 1125px;
    height: 1200px;
  }
  .card {
    position: absolute;
    left: 150px;
    width: 826px;
    height: 471px;
    box-shadow: 0 6px 18px rgba(0, 0, 0, 0.45);
  }
  .card--front {
    top: 98px;
    background: var(--brand-blue);
    color: var(--text-light);
    text-align: center;
  }
  .card--back {
    top: 631px;
    background: var(--card-white);
    text-align: center;
  }
  .identity {
    position: absolute;
    top: 168px;
    left: 0;
    right: 0;
    line-height: 1;
  }
  .identity__name {
    font-size: 31px;
    font-weight: 500;
    letter-spacing: 0.3px;
  }
  .identity__title {
    font-size: 22px;
    font-weight: 400;
  }
  .contact {
    position: absolute;
    top: 214px;
    left: 0;
    right: 0;
    font-size: 20.5px;
    line-height: 27px;
    font-weight: 400;
  }
  .contact__address { margin-top: 4px; }
  .wordmark {
    position: absolute;
    top: 147px;
    left: 0;
    right: 0;
    color: var(--brand-blue);
    font-weight: 500;
    line-height: 1;
  }
  .wordmark__main {
    display: block;
    font-size: 104px;
    letter-spacing: 2px;
  }
  .wordmark__sub {
    display: block;
    margin-top: 30px;
    font-size: 28px;
    letter-spacing: 3px;
  }
  .tagline {
    position: absolute;
    top: 396px;
    left: 0;
    right: 0;
    font-size: 20.5px;
    color: var(--ink-gray);
  }
  .tagline__dot {
    display: inline-block;
    width: 8px;
    height: 8px;
    margin: 0 12px 3px;
    border-radius: 50%;
    background: var(--brand-blue);
    vertical-align: middle;
  }
</style>
</head>
<body>
<main class="stage">
  <section class="card card--front">
    <p class="identity">
      <span class="identity__name">DANIEL HART -</span>
      <span class="identity__title">CEO/FOUNDER</span>
    </p>
    <div class="contact">
      <p>(P) 555 214 3870 (M) 555 382 6148 (F) 555 907 2416</p>
      <p>(E) daniel@norvaleadvisory.com (W)www.norvaleadvisory.com</p>
      <p class="contact__address">(A) 4120 Birchwood Court, Fairview, Oregon 97024</p>
    </div>
  </section>

  <section class="card card--back">
    <p class="wordmark">
      <span class="wordmark__main">NORVALE</span>
      <span class="wordmark__sub">ADVISORY</span>
    </p>
    <p class="tagline">Offering direction<span class="tagline__dot"></span>achieving results</p>
  </section>
</main>
</body>
</html>
```